business card

Business card for new business.
Red and black corporate colors.
Card can have an Indsutrial feel to it. Feel free to add Rust, Bolted steel, or graphics as you see fit. We provide highly specialized services to the below mentioned industries.
Keep information out of corners so that if I want I can choose rounded corners.
Information
- front. name - title - phone - email
- Rear
Refining - Rail - Infrastructure - Mining - Energy
Calgary - Edmonton - Fort McMurray - Revelstoke - Vancouver

```html
<!DOCTYPE html>
<html lang="en">
<head>
<meta charset="utf-8">
<title>Framewell Business Card</title>
<link href="https://fonts.googleapis.com/css2?family=Lato:wght@400;700;900&family=Oswald:wght@600&display=swap" rel="stylesheet">
<style>
  :root {
    --stage: #3b3b3b;
    --card-black: #050505;
    --card-white: #ffffff;
    --brand-red: #e3222b;
    --logo-grey: #8a8a8a;
    --ink: #1a1a1a;
    --light: #ffffff;
  }
  * { box-sizing: border-box; margin: 0; padding: 0; }
  html, body { width: 1200px; height: 1200px; overflow: hidden; }
  body {
    background: var(--stage);
    font-family: "Lato", sans-serif;
    position: relative;
  }
  .card {
    position: absolute;
    left: 150px;
    width: 900px;
    height: 514px;
    overflow: hidden;
  }
  /* Rear side */
  .card-rear { top: 56px; background: var(--card-black); color: var(--light); }
  .rear-brand {
    position: absolute;
    top: 150px; left: 0; right: 0;
    text-align: center;
    font-family: "Lato", sans-serif;
    font-weight: 900;
    font-size: 104px;
    letter-spacing: 2px;
    color: var(--logo-grey);
  }
  .rear-lists {
    position: absolute;
    top: 348px; left: 0; right: 0;
    text-align: center;
    font-size: 27px;
    line-height: 40px;
    letter-spacing: 0.5px;
  }
  .dot {
    display: inline-block;
    width: 7px; height: 7px;
    border-radius: 50%;
    background: var(--brand-red);
    margin: 0 10px;
    vertical-align: middle;
  }
  /* Front side */
  .card-front { top: 626px; background: var(--card-white); color: var(--ink); }
  .identity {
    position: absolute;
    left: 110px; top: 178px;
    text-align: right;
  }
  .person-name {
    font-family: "Oswald", sans-serif;
    font-weight: 600;
    font-size: 66px;
    line-height: 74px;
    color: var(--brand-red);
  }
  .person-title { font-size: 27px; line-height: 30px; }
  .divider {
    position: absolute;
    left: 498px; top: 170px;
    width: 2px; height: 100px;
    background: var(--brand-red);
  }
  .contact-list {
    position: absolute;
    left: 560px; top: 168px;
    list-style: none;
    font-size: 27px;
    line-height: 36px;
  }
  .contact-list li { display: flex; align-items: center; gap: 18px; }
  .contact-list svg { width: 22px; height: 22px; fill: var(--brand-red); flex: none; }
  .address {
    position: absolute;
    left: 0; right: 0; top: 420px;
    text-align: center;
    font-size: 28px;
  }
  .base-band {
    position: absolute;
    left: 0; right: 0; bottom: 0;
    height: 14px;
    background: var(--brand-red);
  }
</style>
</head>
<body>

<section class="card card-rear">
  <div class="rear-brand">FRAMEWELL</div>
  <div class="rear-lists">
    <p>Refining<span class="dot"></span>Rail<span class="dot"></span>Infrastructure<span class="dot"></span>Mining<span class="dot"></span>Energy</p>
    <p>Calgary<span class="dot"></span>Edmonton<span class="dot"></span>Fort McMurray<span class="dot"></span>Revelstoke<span class="dot"></span>Vancouver</p>
  </div>
</section>

<section class="card card-front">
  <div class="identity">
    <div class="person-name">Daniel Hartley</div>
    <div class="person-title">Manager</div>
  </div>
  <div class="divider"></div>
  <ul class="contact-list">
    <li>
      <svg viewBox="0 0 24 24" aria-hidden="true"><path d="M6.6 10.8a15 15 0 0 0 6.6 6.6l2.2-2.2a1 1 0 0 1 1-.25 11.4 11.4 0 0 0 3.6.57 1 1 0 0 1 1 1V20a1 1 0 0 1-1 1A17 17 0 0 1 3 4a1 1 0 0 1 1-1h3.5a1 1 0 0 1 1 1c0 1.25.2 2.45.57 3.57a1 1 0 0 1-.25 1z"/></svg>
      512 555 0142
    </li>
    <li>
      <svg viewBox="0 0 24 24" aria-hidden="true"><path d="M2 5h20v14H2z M2 5l10 8 10-8" stroke="#fff" stroke-width="1.5"/></svg>
      info@framewell.com
    </li>
    <li>
      <svg viewBox="0 0 24 24" aria-hidden="true"><circle cx="12" cy="12" r="10"/><path d="M2 12h20M12 2v20M4.5 7h15M4.5 17h15M12 2c-4 4-4 16 0 20M12 2c4 4 4 16 0 20" stroke="#fff" stroke-width="1.2" fill="none"/></svg>
      www.framewell.com
    </li>
  </ul>
  <div class="address">418 Carver Street, Houston, TX 77041</div>
  <div class="base-band"></div>
</section>

</body>
</html>
```